Brimlow OrthoLink IT Inc. new website

i need a website for my company which is dedicated to installation and service of computer systems in Dental Offices. I would like for it to encompass a technology feel and professional look. The company deals with all aspects of technology like, Audio Visual, computer systems and networks, Cloud services like data backup, data center. We provide manage services, support and services to Dental Professionals.
Updates

Looking for a Technology font but professional look Added Wednesday, April 20, 2016

Target Market(s)

Dental, Dentist

Industry/Entity Type

Dental

Number of Pages Required

5+ page

Font styles to use
Other font styles liked:
• Futuristic or Techy

Colors
0255a3
ec1f27

Requirements
Must have
• Tabs
Nice to have
• Have no idea maybe some suggestion on your part may help
Should not have
• A professional feel but have a techy look

```html
<!DOCTYPE html>
<html lang="en">
<head>
<meta charset="utf-8">
<title>Brimlow OrthoLink IT Inc.</title>
<link href="https://fonts.googleapis.com/css2?family=Lato:wght@700&family=Roboto:wght@300;400;500&display=swap" rel="stylesheet">
<style>
:root{
  --blue:#0255a3;
  --red:#ec1f27;
  --ink:#333;
  --muted:#9a9a9a;
  --page:#f0f0f0;
  --dark:#2e2e2e;
  --footer:#141414;
  --white:#fff;
}
*{box-sizing:border-box;margin:0;padding:0}
html,body{width:693px;height:1200px;overflow:hidden}
body{position:relative;background:var(--page);font-family:'Roboto',Arial,sans-serif;color:var(--ink)}
.abs{position:absolute}

/* header */
.site-header{left:0;top:0;width:693px;height:66px;background:var(--white);border-bottom:1px solid #ddd}
.brand{left:46px;top:16px;display:flex;align-items:center;gap:8px}
.brand-mark{width:14px;height:14px;background:var(--blue)}
.brand-name{font-size:17px;font-weight:500;color:var(--blue);line-height:1.05}
.call{right:18px;top:8px;display:flex;align-items:center;gap:7px;color:var(--red);font-size:12.5px}
.call-icon{width:23px;height:23px;border:1px solid var(--red);border-radius:50%;display:flex;align-items:center;justify-content:center}
.main-nav{right:18px;top:38px;display:flex;gap:0}
.main-nav a{font-size:9.6px;color:#555;text-decoration:none;padding:0 11px;height:28px;line-height:14px}
.main-nav a:last-child{padding-right:0}
.main-nav a.active{color:var(--red);border-bottom:2px solid var(--red)}

/* hero */
.hero{left:0;top:67px;width:693px;height:323px;background:linear-gradient(135deg,#9aa3ab 0%,#c9ced3 40%,#e6e9ec 70%,#b9c0c6 100%)}
.hero-band{left:0;top:168px;width:693px;height:84px;background:rgba(90,95,100,.45)}
.hero-title{left:0;top:197px;width:693px;text-align:center;font-family:'Lato',sans-serif;font-weight:700;font-size:24px;color:var(--white)}

/* services */
.services{left:45px;top:341px;width:603px;height:219px;background:var(--white);border-top:2px solid var(--red)}
.services-strip{left:0;top:0;width:100%;height:18px;background:#efefef}
.service{top:66px;width:180px;height:135px;border:1px solid #e6e6e6;border-bottom:2px solid var(--red);text-align:center;padding-top:38px}
.service-icon{left:64px;top:-27px;width:54px;height:54px;background:var(--red);display:flex;align-items:center;justify-content:center}
.service h3{font-size:10.5px;font-weight:400;color:var(--blue);line-height:14px;padding:0 14px;height:34px}
.service p{font-size:7.6px;color:var(--muted);line-height:13px;padding:6px 10px 0}

/* support */
.support{left:45px;top:560px;width:603px;height:195px;background:var(--dark);color:var(--white);text-align:center}
.support h2{font-size:23px;font-weight:400;margin-top:34px}
.support .lead{font-size:13.5px;margin-top:9px}
.support .contact-line{font-size:11px;margin-top:8px}
.btn-light{display:inline-block;margin-top:14px;background:var(--white);color:var(--blue);font-size:11.5px;padding:11px 13px;text-decoration:none}

/* about */
.about{left:45px;top:755px;width:603px;height:229px;background:var(--white);overflow:hidden}
.about-photo{right:0;top:0;width:260px;height:229px;background:linear-gradient(90deg,#fff 0%,#eef2f6 35%,#dfe6ee 100%)}
.about h2{left:13px;top:28px;font-size:23px;font-weight:400;color:var(--blue)}
.about p{left:13px;top:63px;width:345px;font-size:8.3px;line-height:14.5px;color:var(--muted)}
.btn-red{left:13px;top:155px;background:var(--red);color:var(--white);font-size:11.5px;padding:11px 12px;text-decoration:none}

/* footer */
.site-footer{left:0;top:984px;width:693px;height:180px;background:var(--footer);color:var(--white)}
.col{top:24px;width:140px}
.col h4{font-size:11.5px;font-weight:400;letter-spacing:.3px;margin-bottom:14px}
.quote{font-size:7.8px;line-height:13px;color:#ddd;padding-left:14px;position:relative}
.quote::before{content:"\201C";position:absolute;left:0;top:-4px;color:var(--red);font-size:16px}
.client{display:flex;align-items:center;gap:10px;margin-top:8px;font-size:8.5px;color:var(--red)}
.avatar{width:28px;height:28px;border-radius:50%;background:#c9b8a8;border:2px solid var(--white);flex:none}
.link-item{display:flex;gap:11px;margin-bottom:12px}
.thumb{width:30px;height:30px;border-radius:50%;background:#7d7a6e;flex:none}
.link-item .date{font-size:9px}
.link-item p{font-size:7.8px;line-height:12px;color:#ddd;margin-top:4px}
.touch{display:flex;gap:8px;align-items:flex-start;font-size:7.8px;line-height:11px;margin-bottom:10px}
.touch svg{flex:none}
.news{font-size:8.3px;line-height:14px;color:#ccc}
.news-form{margin-top:14px;display:flex;width:144px;height:36px}
.news-form span{flex:1;background:var(--white);color:#777;font-size:7.6px;line-height:36px;padding-left:8px}
.news-form b{width:36px;background:var(--red);display:flex;align-items:center;justify-content:center}
.arrows{left:176px;top:24px;color:var(--red);font-size:11px}

.bottom-bar{left:0;top:1164px;width:693px;height:36px;background:var(--red);color:var(--footer)}
.bottom-bar .copy{left:46px;top:13px;font-size:7.6px}
.bottom-bar .copy strong{color:var(--white);font-weight:400}
.social{right:44px;top:6px;display:flex;gap:5px}
.social span{width:24px;height:24px;border:1.5px solid var(--white);border-radius:50%}
.social span:first-child{background:var(--white)}
</style>
</head>
<body>

<header class="site-header abs">
  <div class="brand abs"><span class="brand-mark"></span><span class="brand-name">Brimlow<br>OrthoLink</span></div>
  <div class="call abs">CALL US
    <span class="call-icon"><svg width="11" height="11" viewBox="0 0 24 24"><path fill="#ec1f27" d="M6.6 10.8a15 15 0 006.6 6.6l2.2-2.2c.3-.3.7-.4 1-.2 1.1.4 2.3.6 3.6.6.6 0 1 .4 1 1V20c0 .6-.4 1-1 1A17 17 0 013 4c0-.6.4-1 1-1h3.5c.6 0 1 .4 1 1 0 1.3.2 2.5.6 3.6.1.3 0 .7-.2 1z"/></svg></span>
    301-555-0148</div>
  <nav class="main-nav abs">
    <a class="active">HOME</a><a>ABOUT</a><a>SERVICES</a><a>SUPPORT</a><a>CLIENT</a><a>BLOG</a><a>CONTACT</a>
  </nav>
</header>

<section class="hero abs" role="img" aria-label="Photo of a dental treatment chair and equipment in a bright clinic"></section>
<div class="hero-band abs"></div>
<h1 class="hero-title abs">TECHNOLOGY FOR BEST SERVICES</h1>

<section class="services abs">
  <div class="services-strip abs"></div>
  <article class="service abs" style="left:6px">
    <div class="service-icon abs"><svg width="28" height="22" viewBox="0 0 28 22"><rect x="2" y="2" width="24" height="16" rx="2" fill="#1a1a1a"/><rect x="5" y="5" width="18" height="10" fill="#4a8fd8"/></svg></div>
    <h3>AUDIO VISUAL</h3>
    <p>Lorem Ipsum is simply dummy text of the printing and typesetting industry. Lorem Ipsum has been the</p>
  </article>
  <article class="service abs" style="left:212px">
    <div class="service-icon abs"><svg width="34" height="26" viewBox="0 0 34 26"><rect x="8" y="2" width="20" height="14" fill="#fff"/><rect x="10" y="4" width="16" height="10" fill="#2f74c8"/><rect x="14" y="17" width="8" height="3" fill="#ccc"/><rect x="2" y="14" width="9" height="10" fill="#eee"/><rect x="25" y="14" width="8" height="10" fill="#eee"/></svg></div>
    <h3>COMPUTER SYSTEMS AND NETWORKS</h3>
    <p>Lorem Ipsum is simply dummy text of the printing and typesetting industry. Lorem Ipsum has been the</p>
  </article>
  <article class="service abs" style="left:417px">
    <div class="service-icon abs"><svg width="34" height="26" viewBox="0 0 34 26"><ellipse cx="17" cy="10" rx="11" ry="7" fill="#fff"/><rect x="4" y="15" width="12" height="8" fill="#2f74c8"/><rect x="19" y="15" width="12" height="8" fill="#2f74c8"/></svg></div>
    <h3>CLOUD SERVICES OF DATA BACKUP</h3>
    <p>Lorem Ipsum is simply dummy text of the printing and typesetting industry. Lorem Ipsum has been the</p>
  </article>
</section>

<section class="support abs">
  <h2>SUPPORT WITH US</h2>
  <p class="lead">Got unanswered questions? We are Ready to Help You</p>
  <p class="contact-line">email : info@brimlowortholink.com | Call: +(91) 555 010 4821</p>
  <a class="btn-light">CONTACT NOW</a>
</section>

<section class="about abs">
  <div class="about-photo abs" role="img" aria-label="Photo of a smiling dentist in a white coat with arms crossed"></div>
  <h2 class="abs">ABOUT BRIMLOW ORTHOLINK</h2>
  <p class="abs">Lorem Ipsum is simply dummy text of the printing and typesetting industry. Lorem Ipsum has been the industry's standard dummy text ever since the 1500s, when an unknown printer took a galley of type and scrambled it to make a type specimen book. It has survived not only five centuries, but also the leap into electronic typesetting, remaining essentially unchanged. It was popularised in the 1960s with the release of Letraset sheets containing Lorem .</p>
  <a class="btn-red abs">KNOW MORE</a>
</section>

<footer class="site-footer abs">
  <div class="col abs" style="left:46px">
    <h4>TESTIMONIAL</h4>
    <p class="quote">Lorem Ipsum is simply dummy text of the printing and typeing setting industry. Lorem Ipsum is has been the industry's standard ...</p>
    <div class="client"><span class="avatar" role="img" aria-label="Client portrait"></span>CLIENT NAME</div>
  </div>
  <div class="arrows abs">&lsaquo;&rsaquo;</div>
  <div class="col abs" style="left:199px">
    <h4>USEFULL LINK</h4>
    <div class="link-item"><span class="thumb" role="img" aria-label="Post thumbnail"></span><div><div class="date">21/4</div><p>Lorem ipsum dolor sit amet consectetur adipiscing</p></div></div>
    <div class="link-item"><span class="thumb" role="img" aria-label="Post thumbnail" style="background:#a08878"></span><div><div class="date">21/4</div><p>Lorem ipsum dolor sit amet consectetur adipiscing</p></div></div>
  </div>
  <div class="col abs" style="left:352px;width:150px">
    <h4>GET IN TOUCH</h4>
    <div class="touch"><svg width="12" height="14" viewBox="0 0 12 14"><path d="M6 1a4.5 4.5 0 00-4.5 4.5C1.5 9 6 13 6 13s4.5-4 4.5-7.5A4.5 4.5 0 006 1z" fill="none" stroke="#fff"/><circle cx="6" cy="5.5" r="1.5" fill="#fff"/></svg><span>BRIMLOW ORTHOLINK<br>Lorem ipsum dolor amet simple.</span></div>
    <div class="touch"><svg width="12" height="12" viewBox="0 0 24 24"><path fill="none" stroke="#fff" stroke-width="2" d="M6.6 10.8a15 15 0 006.6 6.6l2.2-2.2 4.6 1V20A17 17 0 013 4h4l1 4.6z"/></svg><span>+(91) 555 010 4821</span></div>
    <div class="touch"><svg width="12" height="12" viewBox="0 0 12 12"><rect x="1" y="4" width="10" height="5" fill="none" stroke="#fff"/><rect x="3" y="1" width="6" height="3" fill="none" stroke="#fff"/><rect x="3" y="7" width="6" height="4" fill="none" stroke="#fff"/></svg><span>+(91) 555 010 4821</span></div>
    <div class="touch"><svg width="12" height="10" viewBox="0 0 12 10"><rect x="0.5" y="0.5" width="11" height="9" fill="none" stroke="#fff"/><path d="M.5.5L6 5l5.5-4.5" fill="none" stroke="#fff"/></svg><span>info@brimlowortholink.com</span></div>
  </div>
  <div class="col abs" style="left:504px;width:150px">
    <h4>NEWSLETTER</h4>
    <p class="news">Subscribe to stay on Simple Insurance Leads</p>
    <div class="news-form"><span>Enter your Email</span><b><svg width="16" height="16" viewBox="0 0 16 16"><path d="M1 8l14-6-5 13-2-6z" fill="none" stroke="#fff" stroke-width="1.3"/></svg></b></div>
  </div>
</footer>

<div class="bottom-bar abs">
  <p class="copy abs">© 2016 <strong>BRIMLOW ORTHOLINK</strong> All rights reserved.</p>
  <div class="social abs" aria-label="Social links"><span></span><span></span><span></span><span></span></div>
</div>

</body>
</html>
```